Income Tax Business Cards - Updates

Need to update these business cards while keeping all the same wording but just update them and make them look nicer and more modern/ on brand with our brand.

Industry/Entity Type

finance

Contact Information for Business Card

we have multiple locations so will just need to easily be able to change the address and phone numbers

Colors

Designer to choose colors to be used in the design.

```html
<!DOCTYPE html>
<html lang="en">
<head>
<meta charset="UTF-8">
<title>Tax Business Cards</title>
<link href="https://fonts.googleapis.com/css2?family=Roboto:wght@400;500;700;900&display=swap" rel="stylesheet">
<style>
  :root {
    --page-bg: #d9d4ce;
    --navy: #0c2446;
    --navy-deep: #061630;
    --paper: #f4f5f6;
    --paper-shade: #e6e8ea;
    --ink: #1b1f26;
    --white: #ffffff;
  }
  * { box-sizing: border-box; margin: 0; padding: 0; }
  html, body {
    width: 1200px; height: 800px; overflow: hidden;
    background: var(--page-bg);
    font-family: "Roboto", Arial, sans-serif;
  }
  .canvas { position: relative; width: 1200px; height: 800px; }
  .card {
    position: absolute; top: 245px;
    width: 540px; height: 310px;
    overflow: hidden;
    box-shadow: 0 10px 24px rgba(0,0,0,0.18);
  }
  .card--front { left: 40px; }
  .card--back { left: 620px; }
  .card__surface { position: absolute; inset: 0; }
  .card--front .card__surface {
    background: linear-gradient(160deg, var(--navy) 0%, var(--navy-deep) 100%);
  }
  .card--back .card__surface {
    background: linear-gradient(160deg, var(--white) 0%, var(--paper) 55%, var(--paper-shade) 100%);
  }
  .front-copy {
    position: absolute; inset: 0;
    display: flex; flex-direction: column; align-items: center; justify-content: center;
    color: var(--white); text-align: center; text-transform: uppercase;
  }
  .front-copy__headline { font-weight: 700; font-size: 40px; letter-spacing: 0.5px; margin-bottom: 10px; }
  .front-copy__offer { font-weight: 700; font-size: 22px; line-height: 1.2; }
  .back-art { position: absolute; inset: 0; }
  .offer {
    position: absolute; left: 30px; top: 92px; width: 270px;
    color: var(--white); text-transform: uppercase; font-weight: 700;
  }
  .offer__amount { font-size: 22px; line-height: 1.2; }
  .offer__headline { font-size: 24px; line-height: 1.25; font-weight: 900; }
  .offer__terms { font-size: 13px; font-weight: 500; margin-top: 4px; letter-spacing: 0.3px; }
  .offer__tag {
    display: inline-block; margin-top: 6px; padding: 1px 6px;
    background: var(--white); color: var(--navy);
    font-size: 15px; font-weight: 700;
  }
  .contact {
    position: absolute; right: 24px; top: 36px; width: 190px;
    color: var(--ink); text-align: right;
  }
  .brand { display: flex; align-items: center; justify-content: flex-end; gap: 8px; margin-bottom: 18px; }
  .brand__mark { width: 12px; height: 12px; background: var(--navy); flex: none; }
  .brand__name {
    color: var(--navy); font-weight: 700; font-size: 17px; line-height: 1.1;
  }
  .contact__phone { font-weight: 700; font-size: 23px; margin-bottom: 10px; }
  .contact__address { font-size: 15px; line-height: 1.55; }
</style>
</head>
<body>
<main class="canvas">
  <section class="card card--front">
    <div class="card__surface" role="img" aria-label="Navy background with a subtle geometric cube pattern"></div>
    <div class="front-copy">
      <p class="front-copy__headline">File Your Taxs Here</p>
      <p class="front-copy__offer">Up to $6,000<br>Same Day Advance</p>
    </div>
  </section>

  <section class="card card--back">
    <div class="card__surface" role="img" aria-label="Light background with a subtle geometric cube pattern"></div>
    <svg class="back-art" width="540" height="310" viewBox="0 0 540 310" aria-hidden="true">
      <polygon points="0,70 252,70 312,125 312,215 252,272 0,272" fill="var(--navy)"/>
      <line x1="324" y1="112" x2="322" y2="228" stroke="var(--navy)" stroke-width="3"/>
      <line x1="336" y1="128" x2="334" y2="212" stroke="var(--navy)" stroke-width="3"/>
    </svg>
    <div class="offer">
      <p class="offer__amount">Up to $6,000</p>
      <p class="offer__headline">Same Day Advance</p>
      <p class="offer__terms">On approved tax returns</p>
      <span class="offer__tag">Free Estimates</span>
    </div>
    <div class="contact">
      <div class="brand">
        <span class="brand__mark"></span>
        <span class="brand__name">Harborline Tax Services</span>
      </div>
      <p class="contact__phone">(555)555-5555</p>
      <p class="contact__address">Address Line 1<br>Address Line 1<br>Address Line 1</p>
    </div>
  </section>
</main>
</body>
</html>
```